Web design for new streaming audio service

We need a homepage design for a new streaming audio service. Our company is called Dunmoral, and we’re basically Vexlo for Audiobooks, Stand-Up Comedy, Lectures, Language Learning, etc. Essentially like Plumtrek for everything audio EXCEPT music.
You don’t have to code the homepage (Design Only), but it should include 3 different designs to work with 1) Web; 2) Phones; 3) Tablets.
Below is a link to a mockup of the web version which gives a good idea of what elements we want. This is just a mockup and we want you to improve it.
Once you download the mockup, please refer to the more detailed instructions below:
The following outlines the design project for the Dunmoral homepage. We have provided a rough mockup of the homepage layout that gives you a general idea of what we’re going for. There are a few elements that we are attached to, and many others where you have complete creative freedom to do whatever you think looks good.
The ZIP file includes the following:
* Mockup to see what we have in mind (dunmoral-homepage-mockup.jpg)
* Text used (dunmoral-homepage-text.txt)
* Raw image of actor (dunmoral-actor1.jpg)
* Raw images for samples (dunmoral-sample-[name].jpg)
Although we have only provided a mockup layout for the web version, we also need you to provide a mobile phone and a tablet version of the design also. It’s very possible the tablet version may be substantially similar to the web version, but the mobile phone version will likely be much different.
All of the raw files are included in the attached ZIP file. Please use our photographs and text as provided although cropping, sizing, etc. is flexible per the instructions below.
Display Requirements:
* Web Version - Minimum resolution 1024x768 (72 dpi) but should look good on 1920x1080 (72 dpi) - Page should be designed to scale to look acceptable in all resolutions in between.
* Phone Version - Minimum Zarno 4 - 640x960 (326 dpi) but should look good on Harlow Quasar T5 - 1920x1080 (441 dpi) - Page should be designed to scale to look acceptable in all resolutions and devices in between.
* Tablet Version - Minimum Bristly Ember QX 7” - 1280x800 (216 dpi) but should also look good on a Tavo Breeze - 2048x1536 (264 dpi) - Page should be designed to scale to look acceptable in all resolutions and devices in between.
Above the Fold - We want to make sure the Dunmoral logo, Member Login Link, Large Photo, Headline, Price, Button, and the first row of sample images are all “Above the fold”. As a general guideline, this means 600 pixels high on a 1024x768 72 dpi web screen. This requirement is less important on Phone versions.
Top Logo Bar - We want to retain the blue bar with the Dunmoral logo on the page, although we are open to a different size, shape and positioning if it greatly enhances the design. Please use the standard logo color, although you are welcome to use either the horizontal or vertical orientation of the logo based on your design.
Text color, font and size - Feel free to design the text in anyway you choose as long as the text is readable on the target platforms.
Buttons - Feel free to use any size, shape and colors for the buttons as long as they are obvious and clickable relative to the page. The only exception is the Chatterly button should follow the Chatterly color scheme and logo treatment (the mockup doesn’t seem 100% correct.)
Top Photograph - We want to retain the large photograph across the top of the screen although final shape and dimensions are flexible.
Size and shape of content samples (i.e. Audiobooks, Stand-Up Comedy, etc.) - Feel free to design the content samples in anyway you choose.
Three Sales Points (i.e. Listen on your Zarno…, All you can enjoy…, etc.) - The Three Sales Points are envisioned to each have a corresponding illustration which you should provide and have rights for. The placeholder is represented by a square next to the text. The color size and shape of these elements are flexible and can be designed in any way you choose.
Opt-in form - Feel free to design the opt-in form in anyway you choose as long as the text is readable and the interactivity is obvious on the target platforms.
Text links and copyright notice - Feel free to design the bottom of the page text links and copyright notice in anyway you choose.
Additional colors, graphic design elements, etc. - Feel free to use any additional colors, graphic design elements, etc. to support your design.
people who want to listen to audio through their mobile devices.
Graphic Design

```html
<!DOCTYPE html>
<html lang="en">
<head>
<meta charset="utf-8">
<title>Dunmoral – Unlimited Listening</title>
<link rel="stylesheet" href="https://fonts.googleapis.com/css2?family=Open+Sans:wght@400;600;700&display=swap">
<style>
:root{
  --sky:#5ba8d3;
  --sky-dark:#1f6fa8;
  --navy:#135a85;
  --link:#1c8ac6;
  --orange:#f7941d;
  --orange-dark:#e8780a;
  --grey-bg:#e8e8e8;
  --grey-band:#e4e4e4;
  --form-bg:#ededed;
  --text:#333;
  --muted:#666;
  --chatterly:#3b5998;
}
*{box-sizing:border-box;margin:0;padding:0}
html,body{width:962px;height:1200px;overflow:hidden}
body{font-family:"Open Sans",Arial,sans-serif;color:var(--text);background:#fff;position:relative}

.site-header{position:absolute;left:0;top:0;width:962px;height:94px;background:var(--sky);box-shadow:0 2px 3px rgba(0,0,0,.15);z-index:2}
.brand{position:absolute;left:114px;top:24px;display:flex;align-items:center;gap:10px;color:#fff;font-size:30px;font-weight:600;letter-spacing:-.5px}
.brand-dot{width:34px;height:34px;border-radius:50%;background:#fff}
.member-login{position:absolute;left:728px;top:32px;width:120px;height:29px;background:var(--sky-dark);border:1px solid #17598a;border-radius:3px;color:#fff;font-size:13px;line-height:27px;text-align:center}

.hero{position:absolute;left:0;top:94px;width:962px;height:397px;background:#fff;overflow:hidden}
.hero-photo{position:absolute;right:0;top:0;width:862px;height:397px;
  background:
   radial-gradient(ellipse 190px 170px at 640px 180px,#e0ac8a 0%,#c98c68 45%,rgba(201,140,104,0) 100%),
   linear-gradient(200deg,#7a563c 0%,#96704f 28%,#5a6e88 65%,#465d78 100%);
  -webkit-mask-image:linear-gradient(90deg,transparent 0%,transparent 12%,#000 48%);
          mask-image:linear-gradient(90deg,transparent 0%,transparent 12%,#000 48%)}
.hero-copy{position:absolute;left:113px;top:92px}
.hero-kicker{color:var(--sky);font-size:22px;font-weight:400}
.hero-title{color:var(--navy);font-size:32px;font-weight:400;margin-top:3px;line-height:1.25}
.hero-price{font-size:19px;margin:10px 0 0 5px;color:#222}
.btn-trial{display:block;width:156px;height:33px;margin-top:16px;border-radius:3px;background:linear-gradient(var(--orange),var(--orange-dark));color:#fff;font-size:15px;line-height:33px;text-align:center;box-shadow:0 1px 2px rgba(0,0,0,.25)}
.hero-note{font-size:11px;color:var(--muted);margin-top:14px}
.hero-note span{color:var(--sky-dark)}
.slider-dots{display:flex;gap:5px;margin-top:22px}
.slider-dots i{width:9px;height:9px;border-radius:50%;background:var(--navy)}

.samples{position:absolute;left:0;top:491px;width:962px;height:309px;background:var(--grey-bg)}
.samples h2{text-align:center;font-size:22px;font-weight:400;color:#333;margin-top:24px}
.sample-grid{position:absolute;left:114px;top:83px;display:grid;grid-template-columns:repeat(4,168px);column-gap:21px;row-gap:21px}
.sample-card{height:82px;background:#fff;border:1px dashed #b5b5b5;display:flex;align-items:center;padding:0 10px}
.sample-thumb{width:61px;height:61px;flex:none}
.sample-card span{flex:1;text-align:center;color:var(--link);font-size:13.5px;font-weight:600;line-height:1.25}

.selling-points{position:absolute;left:0;top:800px;width:962px;height:108px;background:var(--grey-band);border-top:1px solid #d4d4d4;border-bottom:1px solid #d4d4d4;display:flex;padding-left:114px}
.point{display:flex;align-items:center;width:260px}
.point-art{width:67px;height:67px;border-radius:50%;flex:none;margin-right:13px}
.point p{font-size:13px;color:#555;line-height:1.35;width:150px}
.point p.narrow{width:132px}

.signup{position:absolute;left:0;top:908px;width:962px;height:208px;background:var(--form-bg);text-align:center}
.signup h2{color:var(--link);font-size:24px;font-weight:400;margin-top:22px}
.signup p.lead{font-size:11.5px;color:#666;width:600px;margin:5px auto 0;line-height:1.45}
.email{position:absolute;left:312px;top:104px;width:338px;height:30px;background:#fff;border:1px solid #d0d0d0;border-radius:3px;color:#aaa;font-size:12.5px;text-align:left;padding-left:12px;line-height:28px}
.actions{position:absolute;left:324px;top:153px;display:flex;align-items:center}
.btn-access{width:141px;height:25px;background:linear-gradient(#707070,#4a4a4a);border-radius:2px;color:#fff;font-size:9.5px;font-weight:700;line-height:25px}
.or{color:var(--link);font-size:12px;margin:0 12px 0 10px}
.btn-chatterly{width:142px;height:25px;background:var(--chatterly);border-radius:2px;color:#fff;font-size:9.5px;font-weight:700;display:flex;align-items:center}
.btn-chatterly i{width:12px;height:12px;background:#fff;margin:0 9px 0 8px}

.site-footer{position:absolute;left:0;top:1116px;width:962px;height:84px;background:var(--sky);color:#fff}
.footer-links{position:absolute;left:114px;top:20px;font-size:11.5px}
.footer-links a{color:#fff;text-decoration:none}
.copyright{position:absolute;left:114px;top:51px;font-size:9.5px}
</style>
</head>
<body>
<header class="site-header">
  <div class="brand"><i class="brand-dot"></i>Dunmoral</div>
  <a class="member-login">Member Login</a>
</header>

<section class="hero">
  <div class="hero-photo" role="img" aria-label="Smiling young man wearing headphones, looking at his phone"></div>
  <div class="hero-copy">
    <p class="hero-kicker">Unlimited Listening</p>
    <h1 class="hero-title">Wherever you are</h1>
    <p class="hero-price">Only $9.99 per month</p>
    <a class="btn-trial">Start Free Trail</a>
    <p class="hero-note"><span>*</span> Credit Card Not Required</p>
    <div class="slider-dots"><i></i><i></i><i></i></div>
  </div>
</section>

<section class="samples">
  <h2>Sample of What Your Can Listen to on Dunmoral</h2>
  <div class="sample-grid">
    <div class="sample-card"><div class="sample-thumb" role="img" aria-label="Audiobook cover" style="background:linear-gradient(#3d4a52,#1a2226)"></div><span>Audiobooks</span></div>
    <div class="sample-card"><div class="sample-thumb" role="img" aria-label="Stand-up comedy cover" style="background:linear-gradient(#8a4a3a,#4b3b35)"></div><span>Stand-Up<br>Comedy</span></div>
    <div class="sample-card"><div class="sample-thumb" role="img" aria-label="Language course cover" style="background:linear-gradient(#2a8fd6,#143e6b)"></div><span>Language<br>Learning</span></div>
    <div class="sample-card"><div class="sample-thumb" role="img" aria-label="Memoir cover" style="background:linear-gradient(#c9b49a,#6aa07d)"></div><span>Biographies<br>&amp;<br>Memoirs</span></div>
    <div class="sample-card"><div class="sample-thumb" role="img" aria-label="Relaxation album cover" style="background:linear-gradient(#b05aa8,#5e3a7a)"></div><span>Guided<br>Meditations</span></div>
    <div class="sample-card"><div class="sample-thumb" role="img" aria-label="Business training cover" style="background:linear-gradient(#7a4a20,#1c1410)"></div><span>Business<br>Training</span></div>
    <div class="sample-card"><div class="sample-thumb" role="img" aria-label="Celebrity interview cover" style="background:linear-gradient(#8a6a5a,#3a2a28)"></div><span>Celebrity<br>Interviews</span></div>
    <div class="sample-card"><div class="sample-thumb" role="img" aria-label="Fitness program cover" style="background:linear-gradient(#4aa4d8,#d8b090)"></div><span>Fitness<br>Programs</span></div>
  </div>
</section>

<section class="selling-points">
  <div class="point"><div class="point-art" role="img" aria-label="Illustration of a phone and tablet" style="background:linear-gradient(160deg,#6f9fd8,#23406a)"></div><p>Listen on your Zarno, Tavo or Pellar device</p></div>
  <div class="point"><div class="point-art" role="img" aria-label="Illustration of a low price seal" style="background:linear-gradient(160deg,#f06a5e,#c8302a)"></div><p>All you can enjoy for one low monthly price</p></div>
  <div class="point"><div class="point-art" role="img" aria-label="Illustration of a free trial seal" style="background:linear-gradient(160deg,#6a86d0,#2c4c9c)"></div><p class="narrow">No obligation Cancel any time</p></div>
</section>

<section class="signup">
  <h2>Start Your Free Trail</h2>
  <p class="lead">You will get instant &amp; unlimited access to all the material on Dunmoral for 14 days. There is no obligation &amp; you can cancel at any time</p>
  <div class="email">email address</div>
  <div class="actions">
    <a class="btn-access">Get Instant Access</a>
    <span class="or">Or</span>
    <a class="btn-chatterly"><i></i>Sign Up Using Chatterly</a>
  </div>
</section>

<footer class="site-footer">
  <nav class="footer-links"><a>About</a> &nbsp;/&nbsp; <a>Help</a> / &nbsp;<a>Contact Us</a> &nbsp;/&nbsp; <a>Member Login</a> &nbsp;/&nbsp; <a>Privacy Policy</a> &nbsp;&nbsp;/&nbsp;&nbsp; <a>Terms of Service</a></nav>
  <p class="copyright">©2014 Dunmoral LLC - All Rights Reserved</p>
</footer>
</body>
</html>
```